Business card for medical clinic

I need an upmarket, modern medical/health business card for my clinic

Contact Information for Business Card

name, address, email, qr code

```html
<!DOCTYPE html>
<html lang="en">
<head>
<meta charset="utf-8">
<title>Meridia Care Clinic – Business Card</title>
<link href="https://fonts.googleapis.com/css2?family=Cinzel:wght@500&family=Arimo:wght@400&display=swap" rel="stylesheet">
<style>
  :root {
    --backdrop: #d2d2d2;
    --card: #ffffff;
    --navy: #1c3553;
    --brand-blue: #1a5f94;
    --accent: #23a3dd;
    --ink: #2b2b2b;
    --rule: #7fb6d8;
  }
  * { box-sizing: border-box; margin: 0; padding: 0; }
  html, body { width: 1200px; height: 915px; overflow: hidden; }
  body {
    background: radial-gradient(ellipse at 50% 40%, #dcdcdc 0%, var(--backdrop) 60%, #c2c2c2 100%);
    font-family: "Arimo", Arial, sans-serif;
    position: relative;
  }
  .card {
    position: absolute;
    width: 540px;
    height: 310px;
    background: var(--card);
    border-radius: 22px;
    box-shadow: 0 6px 18px rgba(0,0,0,0.18);
  }
  .card--front { left: 40px; top: 150px; }
  .card--back { left: 620px; top: 455px; }

  .brand {
    display: flex;
    align-items: center;
    gap: 12px;
    font-family: "Cinzel", Georgia, serif;
    font-weight: 500;
    color: var(--brand-blue);
    letter-spacing: 1px;
    white-space: nowrap;
  }
  .brand__dot {
    border-radius: 50%;
    background: var(--accent);
    flex: none;
  }
  .card--front .brand {
    position: absolute;
    left: 50%; top: 50%;
    transform: translate(-50%, -50%);
    font-size: 30px;
  }
  .card--front .brand__dot { width: 18px; height: 18px; }

  .card--back .brand {
    position: absolute;
    left: 130px; top: 46px;
    font-size: 22px;
  }
  .card--back .brand__dot { width: 13px; height: 13px; }

  .holder {
    position: absolute;
    left: 40px; top: 142px;
    width: 220px;
    text-align: right;
  }
  .holder__name {
    font-family: "Cinzel", Georgia, serif;
    font-weight: 500;
    font-size: 23px;
    color: var(--brand-blue);
    letter-spacing: 0.5px;
  }
  .holder__role {
    font-size: 13px;
    color: var(--ink);
    margin-top: 2px;
  }
  .divider {
    position: absolute;
    left: 280px; top: 112px;
    width: 1px; height: 92px;
    background: var(--rule);
  }
  .contacts {
    position: absolute;
    left: 298px; top: 116px;
    list-style: none;
  }
  .contacts__item {
    display: flex;
    align-items: center;
    gap: 8px;
    font-size: 13px;
    color: var(--ink);
    line-height: 28px;
  }
  .contacts__icon { width: 12px; height: 12px; flex: none; fill: var(--accent); }
  .address {
    position: absolute;
    left: 0; right: 0; bottom: 40px;
    text-align: center;
    font-size: 13px;
    color: var(--ink);
  }
</style>
</head>
<body>

  <section class="card card--front" aria-label="Card front">
    <div class="brand"><span class="brand__dot"></span>Meridia Care Clinic</div>
  </section>

  <section class="card card--back" aria-label="Card back">
    <div class="brand"><span class="brand__dot"></span>Meridia Care Clinic</div>

    <div class="holder">
      <p class="holder__name">Daniel Harlow</p>
      <p class="holder__role">Director/Founder</p>
    </div>

    <div class="divider"></div>

    <ul class="contacts">
      <li class="contacts__item">
        <svg class="contacts__icon" viewBox="0 0 12 12" aria-hidden="true"><path d="M2.5 1 L4.5 1 L5.2 3.6 L4 4.6 C4.7 6 6 7.3 7.4 8 L8.4 6.8 L11 7.5 L11 9.5 C11 10.3 10.3 11 9.5 11 C5 11 1 7 1 2.5 C1 1.7 1.7 1 2.5 1 Z"/></svg>
        05317 480 2293
      </li>
      <li class="contacts__item">
        <svg class="contacts__icon" viewBox="0 0 12 12" aria-hidden="true"><path d="M1 2.5 H11 V9.5 H1 Z M1.6 3 L6 6.6 L10.4 3 Z" fill-rule="evenodd"/></svg>
        info@meridiacareclinic.com
      </li>
      <li class="contacts__item">
        <svg class="contacts__icon" viewBox="0 0 12 12" aria-hidden="true"><circle cx="6" cy="6" r="5"/><path d="M1 6 H11 M6 1 C3.5 3.5 3.5 8.5 6 11 M6 1 C8.5 3.5 8.5 8.5 6 11" stroke="#fff" stroke-width="0.8" fill="none"/></svg>
        www.meridiacareclinic.com
      </li>
    </ul>

    <p class="address">1187 Linden Avenue Westbrook AV 60318</p>
  </section>

</body>
</html>
```